Corvane Paintless Dent Removal

Our company works on vehicles removing dents using a highly skilled trade which the metal is massaged out with special tools without disturbing the original paint, hence paintless dent removal. Besides keeping the paint and metal original its also very environmentally friendly since no paint or toxic fillers are used. Also we we are one of the most experienced companies in the business with 25 years

Target Market(s)

Retail Automobile consumers, Auto Dealerships and Auto Body Shops

Industry/Entity Type

Auto Repair

Contact Information for Business Card

Dale Hollister
PO Box 518 Brookmere, NY 11962
631-555-0148
corvanepdr@mailbox-example.com
website corvanepdr.example
youtube corvane paintless dent removal
25 years of experience removing Dents, Dings and Hail Damage

Font styles to use
Serif
Sans Serif

Colors

Designer to choose colors to be used in the design.

Requirements
Must have
• I do like things that are simple but classy and somewhat bold, also I like my logo so that should be somewhat important

```html
<!DOCTYPE html>
<html lang="en">
<head>
<meta charset="utf-8">
<title>Corvane Paintless Dent Removal — Business Card</title>
<link rel="stylesheet" href="https://fonts.googleapis.com/css2?family=Roboto:wght@400;700&family=Montserrat:wght@600&display=swap">
<style>
  :root {
    --navy: #10284b;
    --green: #72bb1a;
    --paper: #f4f4f2;
    --gold: #c8962a;
    --gold-dark: #7a5412;
    --grey-text: #555a60;
    --backdrop: #e7e4df;
    --white: #ffffff;
  }
  * { margin: 0; padding: 0; box-sizing: border-box; }
  html, body { width: 1200px; height: 960px; overflow: hidden; }
  body {
    background: var(--backdrop);
    font-family: "Roboto", Arial, sans-serif;
    position: relative;
  }
  .card {
    position: absolute;
    width: 600px;
    height: 343px;
    background: var(--paper);
    overflow: hidden;
    box-shadow: 0 3px 8px rgba(0,0,0,0.25);
  }
  .card-front { left: 314px; top: 113px; }
  .card-back  { left: 311px; top: 472px; }

  .front-shape { position: absolute; inset: 0; }

  .holder-name {
    position: absolute;
    left: 39px; top: 45px;
    font-family: "Montserrat", Arial, sans-serif;
    font-weight: 600;
    font-size: 19px;
    letter-spacing: 0.3px;
    color: var(--white);
  }
  .experience-seal {
    position: absolute;
    left: 39px; top: 79px;
    width: 70px; height: 70px;
    border-radius: 50%;
    background: radial-gradient(circle, #e9b949 0 45%, var(--gold) 46% 60%, var(--gold-dark) 61% 100%);
    display: flex; flex-direction: column; align-items: center; justify-content: center;
    color: #2a1c05;
    font-weight: 700;
    line-height: 1;
  }
  .experience-seal .years-number { font-size: 20px; }
  .experience-seal .years-label { font-size: 8px; letter-spacing: 0.5px; }

  .address {
    position: absolute;
    left: 39px; top: 183px;
    color: var(--white);
    font-size: 14.5px;
    line-height: 19px;
  }
  .contact-list {
    position: absolute;
    left: 39px; top: 226px;
    list-style: none;
    color: var(--white);
    font-size: 14.5px;
    line-height: 19.3px;
  }
  .contact-list li { display: flex; align-items: center; gap: 8px; }
  .contact-list svg { width: 15px; height: 13px; flex: none; }

  .wordmark {
    position: absolute;
    text-align: center;
    color: var(--navy);
    font-weight: 700;
    line-height: 1;
  }
  .wordmark .brand { display: block; letter-spacing: -0.5px; }
  .wordmark .service { display: block; }
  .card-front .wordmark { left: 290px; top: 148px; width: 270px; }
  .card-front .wordmark .brand { font-size: 31px; }
  .card-front .wordmark .service { font-size: 14px; margin-top: 2px; }
  .card-back .wordmark { left: 130px; top: 141px; width: 340px; }
  .card-back .wordmark .brand { font-size: 40px; }
  .card-back .wordmark .service { font-size: 18px; margin-top: 3px; }

  .back-url {
    position: absolute;
    left: 0; right: 0; top: 279px;
    text-align: center;
    font-size: 14px;
    letter-spacing: 5.2px;
    color: var(--grey-text);
  }
</style>
</head>
<body>

<section class="card card-front" aria-label="Business card front">
  <svg class="front-shape" viewBox="0 0 600 343" width="600" height="343" aria-hidden="true">
    <rect width="600" height="343" fill="var(--navy)"/>
    <path d="M362 0 C232 30 150 250 470 343 L600 343 L600 0 Z" fill="var(--white)"/>
    <path d="M365 0 C238 32 158 250 480 343 L600 343 L600 0 Z" fill="var(--green)"/>
    <path d="M392 0 C248 45 170 250 500 343 L600 343 L600 0 Z" fill="var(--paper)"/>
  </svg>

  <h1 class="holder-name">DALE HOLLISTER</h1>

  <div class="experience-seal" aria-label="25 years of experience">
    <span class="years-number">25</span>
    <span class="years-label">YEARS</span>
  </div>

  <p class="address">PO Box 518<br>Brookmere, NY 11962</p>

  <ul class="contact-list">
    <li>
      <svg viewBox="0 0 16 16" aria-hidden="true"><path fill="#fff" d="M3.6 1.2l2.3 2.6-1.3 1.8c.9 1.9 2.2 3.3 4.3 4.5l1.8-1.3 2.6 2.3-1.3 2.3C7.3 13.2 2.6 8.6 1.3 2.5z"/></svg>
      <span>631-555-0148</span>
    </li>
    <li>
      <svg viewBox="0 0 16 16" aria-hidden="true"><rect x="1.5" y="3.5" width="13" height="9" fill="#fff"/><path d="M1.5 3.5 8 9l6.5-5.5" fill="none" stroke="var(--navy)" stroke-width="1.3"/></svg>
      <span>corvanepdr@mailbox-example.com</span>
    </li>
    <li>
      <svg viewBox="0 0 16 16" aria-hidden="true"><circle cx="8" cy="8" r="6.3" fill="#fff"/><path d="M4 6.5c2 0 2 2 3.5 2.5s1 3 2.5 3M9 2.2c-.5 1.5 1 2 2.5 2" fill="none" stroke="var(--navy)" stroke-width="1.2"/></svg>
      <span>corvanepdr.example</span>
    </li>
    <li>
      <svg viewBox="0 0 16 16" aria-hidden="true"><rect x="3" y="3" width="10" height="10" fill="#fff"/></svg>
      <span>corvane paintless dent removal</span>
    </li>
  </ul>

  <div class="wordmark">
    <span class="brand">CORVANE</span>
    <span class="service">Paintless Dent Removal</span>
  </div>
</section>

<section class="card card-back" aria-label="Business card back">
  <div class="wordmark">
    <span class="brand">CORVANE</span>
    <span class="service">Paintless Dent Removal</span>
  </div>
  <p class="back-url">www.corvanepdr.example</p>
</section>

</body>
</html>
```